Recto Verso Audiology Business Card

Business card with a beautiful design on the back. On the Recto you need the following data Lindqvist Oren Audiologist Hearing Solutions Hearing Protection Tinnitus Hyperacusis Tel: 0482/37 59 08 Email: On the back, you need something nice like the attached file. The logo "Corra Luna" can be in the center The colors of the Logo can not be changed If possible stay in the same colors as the logo Another solution is to put the logo on the front and have a nice back (A mosaic of small ears, hearing aids or other ..) Thank you _______________________________________________________________ Visit card On the Recto Lindqvist Oren Audiologist Hearing Solutions Hearing Protection Tinnitus Hyperacusis Tel: 0482/37 59 08 Email: You can put the logo " Corra Luna "on the Recto of the Verso The colors of the logo can not be changed. If you put the logo on the back, it must be well integrated. On the Verso I need something in the files. something stylish. It's a visit card for an audiologist. You can get ears of hearing aids if you need. Thanks

Target Market(s)

customers

Contact Information for Business Card

Carte de visite standard ou A6

Font styles to use
Serif
Sans Serif

Colors
33a6d7

Requirements
Must have
• the logo and a stylized background.
Nice to have
• It would be nice to have a back side related to audiology (ears, hearing aids etc.)

```html
<!DOCTYPE html>
<html lang="en">
<head>
<meta charset="utf-8">
<title>Corra Luna – Audiology Business Card</title>
<link rel="stylesheet" href="https://fonts.googleapis.com/css2?family=Ubuntu+Condensed&display=swap">
<style>
  :root {
    --backdrop: #d8d3cc;
    --card: #2b2c2e;
    --pattern-deep: #202a30;
    --pattern-mid: #263a42;
    --pattern-teal: #2e5560;
    --teal: #3fb3c9;
    --muted: #5f7480;
    --ink: #f1f2f2;
    --rule: #8a8d90;
  }
  * { box-sizing: border-box; margin: 0; padding: 0; }
  html, body {
    width: 1200px; height: 419px; overflow: hidden;
    background: var(--backdrop);
    font-family: "Ubuntu Condensed", "Arial Narrow", sans-serif;
  }
  .stage {
    position: relative; width: 1200px; height: 419px;
    display: flex; align-items: center; justify-content: center; gap: 80px;
  }
  .card {
    position: relative; width: 480px; height: 300px;
    background: var(--card);
    box-shadow: 0 10px 24px rgba(0,0,0,.28);
    overflow: hidden;
  }

  /* Front: stylised audiology pattern area with the name block */
  .card-front .pattern-area {
    position: absolute; inset: 0;
    background:
      radial-gradient(ellipse at 50% 50%, var(--pattern-teal) 0%, var(--pattern-mid) 45%, var(--pattern-deep) 100%);
  }
  .name-block {
    position: absolute; left: 50%; top: 50%;
    transform: translate(-50%, -50%);
    display: flex; align-items: center; gap: 12px;
    padding: 16px 22px;
    background: var(--card);
    border: 1px solid var(--teal);
    white-space: nowrap;
  }
  .name-square {
    flex: none; width: 14px; height: 14px; border: 2px solid var(--teal);
  }
  .name-text {
    color: var(--teal); font-size: 28px; letter-spacing: 2px;
    text-transform: uppercase; line-height: 1;
  }

  /* Back: contact details */
  .card-back .frame {
    position: absolute; inset: 16px;
    border: 1px solid var(--rule);
  }
  .details {
    position: absolute; left: 135px; top: 92px; width: 300px;
    text-align: center; color: var(--ink);
    white-space: nowrap;
  }
  .person-name {
    font-weight: 400;
    color: var(--teal); font-size: 20px; text-transform: uppercase; letter-spacing: .5px;
    line-height: 1.1;
  }
  .person-role { color: var(--muted); font-size: 14px; line-height: 1.3; }
  .contact { font-size: 13px; line-height: 1.5; }
  .contact .web { letter-spacing: 3px; }
  .divider {
    height: 1px; margin: 6px 30px;
    background: linear-gradient(90deg, transparent, var(--rule), transparent);
  }
  .services { font-size: 14px; line-height: 1.35; }
</style>
</head>
<body>
  <main class="stage">
    <section class="card card-front">
      <div class="pattern-area" role="img" aria-label="Stylised audiology background: a repeating mosaic of small ears with sound waves in teal on charcoal"></div>
      <div class="name-block">
        <span class="name-square"></span>
        <span class="name-text">Corra Luna</span>
      </div>
    </section>

    <section class="card card-back">
      <div class="frame"></div>
      <div class="details">
        <h1 class="person-name">Lindqvist Oren</h1>
        <p class="person-role">Audiologist Hearing</p>
        <div class="divider"></div>
        <div class="contact">
          <p>[P] 0482/37 59 08 [E] hello@corraluna.be</p>
          <p class="web">www.corraluna.be</p>
        </div>
        <div class="divider"></div>
        <p class="services">Solutions Hearing | Protection<br>Tinnitus | Hyperacusis</p>
      </div>
    </section>
  </main>
</body>
</html>
```